Wellness, Meaning, and the Inner Journey Research Program Website

Overview: This website will serve a new research program (Wellness, Meaning, and the Inner Journey) at the Harrowgate University School of Medicine. I want a clean, intuitive design that has a navigation bar, but uses icons/graphic buttons to link to the main pages. In an attached Word document, I have provided a basic information architecture for the site, understanding that this project would just generate graphics and code for the 3 pages. I highlighted the 3 pages I'd like designed.
Target market: People who want to participate in our research, or contribute grant funding to specific projects.
Number of page: The design project focuses on 3 pages, but the site must accommodate 6 pages with top-level links. See attached Word doc.
Logo and website header: Please integrate our logo in the header. I've uploaded it as a png file--both with the name of the website and with just the logo image. I imaging the logo would look great in a banner set against an image of a mountain. The two main design themes I want to see included are nature and healthcare.
Text content: I have not yet provided text. Use some dummy text.
Technical Specifications:
- Build using WordPress. We will host this site ourselves on NetHarbor using WordPress.
- The design package must be coded.
- The template must be responsive to different platforms (e.g., computer, mobile phone, iPad).
Thank you! I look forward to seeing your designs.
- Ned

```html
<!DOCTYPE html>
<html lang="en">
<head>
<meta charset="utf-8">
<title>Wellness, Meaning, and the Inner Journey – The Research Program</title>
<link href="https://fonts.googleapis.com/css2?family=Montserrat:wght@400;500;600;700;800&family=Open+Sans:wght@400;600&display=swap" rel="stylesheet">
<style>
:root{
  --blue:#1a4f8b;
  --blue-deep:#0f5aa8;
  --green:#6a9a2a;
  --green-bright:#7cb52e;
  --ink:#1f1f1f;
  --text:#333333;
  --soft:#f3f0ef;
  --footer:#1c1c1c;
  --footer-line:#3a3a3a;
  --white:#ffffff;
}
*{margin:0;padding:0;box-sizing:border-box}
html,body{width:1200px;height:3418px;overflow:hidden}
body{position:relative;font-family:"Open Sans",Arial,sans-serif;color:var(--text);background:var(--white)}
.abs{position:absolute}
.btn{position:absolute;background:var(--green);color:var(--white);font-family:Montserrat,Arial,sans-serif;font-weight:700;display:flex;align-items:center;justify-content:center;letter-spacing:.2px;text-decoration:none}

/* header */
.site-header{position:absolute;left:0;top:0;width:1200px;height:92px;background:var(--white)}
.brand{position:absolute;left:133px;top:28px;display:flex;align-items:center;gap:10px}
.brand-dot{width:34px;height:34px;border-radius:50%;background:var(--green)}
.brand-name{font-family:Montserrat,Arial,sans-serif;font-weight:700;font-size:14px;line-height:17px;color:var(--blue);width:270px}
.main-nav a{position:absolute;top:38px;font-family:Montserrat,Arial,sans-serif;font-size:13px;font-weight:500;color:var(--ink);text-decoration:none}
.main-nav a.active{color:var(--green);font-weight:700;font-size:14px}
.main-nav a.active::before{content:"";position:absolute;left:0;right:0;top:-9px;height:2px;background:var(--green)}
.main-nav a.active::after{content:"";position:absolute;left:0;right:0;bottom:-9px;height:2px;background:var(--green)}

/* hero */
.hero{position:absolute;left:0;top:92px;width:1200px;height:550px;
  background:linear-gradient(180deg,#7fa6ae 0%,#9db7b2 35%,#c7c3b0 55%,#8a7a6a 72%,#3b2b22 100%)}
.hero-title{position:absolute;left:303px;top:86px;font-family:Montserrat,Arial,sans-serif;font-weight:800;font-size:46px;line-height:50px;color:var(--blue)}
.hero-text{position:absolute;left:307px;top:196px;font-family:Montserrat,Arial,sans-serif;font-size:17px;line-height:23px;color:#1e2a30;width:360px}
.hero-figure{position:absolute;left:700px;top:30px;width:340px;height:420px;border-radius:40% 40% 30% 30%;background:radial-gradient(ellipse at center,rgba(60,40,40,.35),rgba(60,40,40,0) 70%)}
.dots{position:absolute;display:flex;gap:11px;align-items:center}
.dots span{width:6px;height:6px;border-radius:50%;background:var(--white)}
.dots span.on{width:11px;height:11px;border:2px solid var(--white);background:var(--blue-deep)}

/* section titles */
.section-title{position:absolute;font-family:Montserrat,Arial,sans-serif;font-weight:800;color:var(--blue);text-align:center}
.title-rule{position:absolute;height:1px;background:#7a9cbf}
.title-rule.under{background:var(--green)}
.dot-b,.dot-g{position:absolute;width:10px;height:10px;border-radius:50%}
.dot-b{background:var(--blue)}
.dot-g{background:var(--green)}

/* services */
.services-text{position:absolute;left:132px;top:810px;width:255px;font-size:14.5px;line-height:22.3px;color:var(--ink)}
.venn-label{position:absolute;font-family:Montserrat,Arial,sans-serif;font-weight:700;font-size:16px;color:var(--white);text-align:center;width:200px}

/* people */
.people{position:absolute;left:0;top:1127px;width:1200px;height:606px;background:var(--soft)}
.person{position:absolute;width:230px;text-align:center}
.person-photo{width:190px;height:190px;border-radius:50%;margin:0 auto}
.person-name{margin-top:30px;font-family:Montserrat,Arial,sans-serif;font-weight:600;font-size:16px;color:var(--ink);letter-spacing:.3px}
.person-text{margin:12px auto 0;width:175px;font-size:12.3px;line-height:17.5px;color:var(--ink)}
.person .btn{position:relative;margin:20px auto 0;width:84px;height:29px;font-size:10.5px}
.people .dots span{background:#b9b4b2}
.people .dots span.on{width:6px;height:6px;border:none;background:var(--blue)}

/* projects */
.project{position:absolute;width:299px}
.project-img{width:299px;height:215px}
.project-label{margin-top:12px;font-family:Montserrat,Arial,sans-serif;font-weight:700;font-size:15.5px;color:var(--ink);margin-left:-2px}

/* faq */
.faq{position:absolute;left:0;top:2548px;width:1200px;height:541px;
  background:linear-gradient(180deg,#fbf1ea 0%,#f6e2d2 40%,#e9c6a0 62%,#b88c55 82%,#6a5a33 100%)}
.faq-scene{position:absolute;left:520px;top:160px;width:640px;height:381px;background:radial-gradient(ellipse at 60% 55%,rgba(120,110,110,.35),rgba(120,110,110,0) 65%)}
.faq-item{position:absolute;left:132px;font-family:Montserrat,Arial,sans-serif;font-size:16.5px;color:var(--ink);border-bottom:1.5px solid #2a2a2a;padding-bottom:11px;display:flex;align-items:center;gap:18px}
.faq-toggle{width:22px;height:22px;border:1.5px solid #2a2a2a;border-radius:50%;display:flex;align-items:center;justify-content:center;flex:none}

/* footer */
.site-footer{position:absolute;left:0;top:3089px;width:1200px;height:329px;background:var(--footer);color:var(--white)}
.footer-brand{position:absolute;left:133px;top:72px;display:flex;align-items:center;gap:14px;width:300px}
.footer-brand-dot{width:40px;height:40px;border-radius:50%;background:var(--green);flex:none}
.footer-brand-name{font-family:Montserrat,Arial,sans-serif;font-weight:700;font-size:17px;line-height:22px;color:var(--white)}
.footer-heading{position:absolute;font-family:Montserrat,Arial,sans-serif;font-weight:700;font-size:11.5px;letter-spacing:.3px}
.footer-menu{position:absolute;left:430px;top:82px;list-style:none}
.footer-menu li{font-family:Montserrat,Arial,sans-serif;font-size:12px;line-height:20px;color:var(--white)}
.contact-icon{position:absolute;width:36px;height:36px;border-radius:50%;background:var(--white);display:flex;align-items:center;justify-content:center}
.contact-text{position:absolute;font-family:Montserrat,Arial,sans-serif;font-size:13.5px;line-height:19px}
.social{position:absolute;width:27px;height:27px;border-radius:50%}
.footer-rule{position:absolute;left:133px;top:244px;width:930px;height:1px;background:var(--footer-line)}
.copyright{position:absolute;left:0;top:283px;width:1200px;text-align:center;font-family:Montserrat,Arial,sans-serif;font-size:11.5px;color:#d8d8d8}
</style>
</head>
<body>

<header class="site-header">
  <div class="brand">
    <div class="brand-dot"></div>
    <div class="brand-name">Wellness, Meaning, and the Inner Journey<br>The Research Program</div>
  </div>
  <nav class="main-nav">
    <a class="active" style="left:541px">HOME</a>
    <a style="left:617px">PEOPLE</a>
    <a style="left:712px">PROJECTS</a>
    <a style="left:818px">FAQS</a>
    <a style="left:892px">RESOURCES</a>
    <a style="left:1004px">CONTACT</a>
  </nav>
</header>

<section class="hero" role="img" aria-label="Photo of a person leaping joyfully above snowy mountain slopes at dusk">
  <div class="hero-figure"></div>
  <h1 class="hero-title">THE RESEARCH<br>PROGRAM</h1>
  <p class="hero-text">Lorem Ipsum is simply dummy text of the printing and typesetting industry</p>
  <a class="btn" style="left:309px;top:266px;width:138px;height:40px;font-size:15px">READ MORE</a>
  <div class="dots" style="left:563px;top:506px">
    <span></span><span></span><span class="on"></span><span></span><span></span>
  </div>
</section>

<!-- services -->
<section class="services">
  <div class="title-rule" style="left:124px;top:723px;width:192px"></div>
  <div class="dot-b" style="left:315px;top:718px"></div>
  <h2 class="section-title" style="left:129px;top:729px;font-size:27px">OUR SERVICES</h2>
  <div class="title-rule under" style="left:126px;top:766px;width:192px"></div>
  <div class="dot-g" style="left:121px;top:762px"></div>
  <p class="services-text">There are many variations of passages of Lorem Ipsum available, but the majority have suffered alteration in some form, by injected humour, or randomised words which don't look even slightly believable. If you are going to use a passage.</p>
  <a class="btn" style="left:131px;top:1005px;width:125px;height:37px;font-size:14px">READ MORE</a>

  <svg class="abs" style="left:486px;top:692px" width="582" height="376" viewBox="0 0 582 376" role="img" aria-label="Overlapping circles with healthcare and nature photos: hands holding a heart, and children playing in a green meadow">
    <defs>
      <radialGradient id="blueFill" cx="45%" cy="50%" r="60%">
        <stop offset="0" stop-color="#2a6fc0"/><stop offset="1" stop-color="#0d4f9c"/>
      </radialGradient>
      <radialGradient id="greenFill" cx="50%" cy="40%" r="60%">
        <stop offset="0" stop-color="#93c94a"/><stop offset="1" stop-color="#4c8f1f"/>
      </radialGradient>
      <clipPath id="blueClip"><circle cx="187" cy="188" r="187"/></clipPath>
    </defs>
    <circle cx="187" cy="188" r="187" fill="url(#blueFill)"/>
    <circle cx="394" cy="188" r="187" fill="url(#greenFill)"/>
    <circle cx="394" cy="188" r="187" fill="#2a8a6a" clip-path="url(#blueClip)"/>
    <g fill="none" stroke="#fff" stroke-width="2">
      <circle cx="110" cy="155" r="40"/>
      <circle cx="286" cy="155" r="40"/>
      <circle cx="477" cy="155" r="40"/>
    </g>
    <!-- heart pulse icon -->
    <path d="M110 172 l-18 -18 a10 10 0 0 1 18 -14 a10 10 0 0 1 18 14 z" fill="#fff"/>
    <polyline points="90,156 102,156 106,149 111,164 115,153 130,153" fill="none" stroke="#0d4f9c" stroke-width="2.5"/>
    <!-- diamond icon -->
    <path d="M272 144 h28 l9 10 -23 24 -23 -24 z" fill="#fff"/>
    <path d="M263 154 h46 M281 144 l-4 10 9 24 9 -24 -4 -10" fill="none" stroke="#2a8a6a" stroke-width="1.6"/>
    <!-- sprout icon -->
    <path d="M477 178 v-22" stroke="#fff" stroke-width="3"/>
    <path d="M477 160 c-10 -2 -16 -10 -16 -18 c10 2 16 10 16 18 z M477 160 c10 -2 16 -10 16 -18 c-10 2 -16 10 -16 18 z" fill="#fff"/>
    <circle cx="477" cy="136" r="4" fill="#fff"/>
  </svg>
  <div class="venn-label" style="left:490px;top:909px">HEALTHCARE</div>
  <div class="venn-label" style="left:675px;top:909px">VALUES</div>
  <div class="venn-label" style="left:863px;top:909px">SPIRITUAL LIFE</div>
</section>

<section class="people">
  <div class="title-rule" style="left:548px;top:48px;width:104px"></div>
  <div class="dot-b" style="left:648px;top:43px"></div>
  <h2 class="section-title" style="left:500px;top:52px;width:200px;font-size:26px">PEOPLE</h2>
  <div class="title-rule under" style="left:548px;top:91px;width:104px"></div>
  <div class="dot-g" style="left:540px;top:86px"></div>

  <div class="person" style="left:113px;top:145px">
    <div class="person-photo" role="img" aria-label="Portrait photo of researcher Owen Hale" style="background:linear-gradient(160deg,#9b8f86,#4a4540)"></div>
    <div class="person-name">OWEN HALE</div>
    <p class="person-text">There are many variations of passages of Lorem Ipsum available, but the majority have suffered alter.</p>
    <a class="btn">VIEW BIO</a>
  </div>
  <div class="person" style="left:351px;top:145px">
    <div class="person-photo" role="img" aria-label="Portrait photo of researcher Carver" style="background:linear-gradient(160deg,#8a8682,#3a3836)"></div>
    <div class="person-name">CARVER</div>
    <p class="person-text">There are many variations of passages of Lorem Ipsum available, but the majority have suffered alter.</p>
    <a class="btn">VIEW BIO</a>
  </div>
  <div class="person" style="left:596px;top:145px">
    <div class="person-photo" role="img" aria-label="Portrait photo of researcher Lindqvist by the water" style="background:linear-gradient(160deg,#b9cfdc,#7a95a8)"></div>
    <div class="person-name">LINDQVIST</div>
    <p class="person-text">There are many variations of passages of Lorem Ipsum available, but the majority have suffered alter.</p>
    <a class="btn">VIEW BIO</a>
  </div>
  <div class="person" style="left:858px;top:145px">
    <div class="person-photo" role="img" aria-label="Portrait photo of researcher Rowan" style="background:linear-gradient(160deg,#3a3a3a,#151515)"></div>
    <div class="person-name">ROWAN</div>
    <p class="person-text">There are many variations of passages of Lorem Ipsum available, but the majority have suffered alter.</p>
    <a class="btn">VIEW BIO</a>
  </div>

  <div class="dots" style="left:561px;top:553px">
    <span></span><span></span><span class="on"></span><span></span><span></span>
  </div>
</section>

<section class="projects">
  <div class="title-rule" style="left:461px;top:1799px;width:270px"></div>
  <div class="dot-b" style="left:727px;top:1794px"></div>
  <h2 class="section-title" style="left:400px;top:1803px;width:400px;font-size:26px">RESEARCH PROJECTS</h2>
  <div class="title-rule under" style="left:464px;top:1842px;width:274px"></div>
  <div class="dot-g" style="left:460px;top:1838px"></div>

  <div class="project" style="left:130px;top:1890px">
    <div class="project-img" role="img" aria-label="Photo of a tablet and stethoscope with a glowing digital health network" style="background:linear-gradient(135deg,#e4edf3,#9fb6c6 60%,#5e7585)"></div>
    <div class="project-label">PROJECT 1</div>
  </div>
  <div class="project" style="left:451px;top:1890px">
    <div class="project-img" role="img" aria-label="Photo of a misty green rainforest" style="background:linear-gradient(180deg,#8fae86,#3f6b33 55%,#1f3d1c)"></div>
    <div class="project-label">PROJECT 2</div>
  </div>
  <div class="project" style="left:770px;top:1890px">
    <div class="project-img" role="img" aria-label="Photo of a family running through a golden field at sunset" style="background:linear-gradient(180deg,#f3e6c4,#d8b06a 55%,#7d5a2d)"></div>
    <div class="project-label">PROJECT 3</div>
  </div>
  <div class="project" style="left:130px;top:2156px">
    <div class="project-img" role="img" aria-label="Photo looking up into a sunlit tree canopy" style="background:radial-gradient(circle at 55% 45%,#d6e98a,#7fae2f 45%,#3f6e1b)"></div>
    <div class="project-label">PROJECT 4</div>
  </div>
  <div class="project" style="left:451px;top:2156px">
    <div class="project-img" role="img" aria-label="Photo of a woman with arms raised against a warm sunset" style="background:linear-gradient(180deg,#b9a7c4,#f0c48a 50%,#b86a2e)"></div>
    <div class="project-label">PROJECT 5</div>
  </div>
  <div class="project" style="left:770px;top:2156px">
    <div class="project-img" role="img" aria-label="Photo of a tablet showing a digital body scan and health charts" style="background:linear-gradient(135deg,#c9d6e2,#1f4f78 35%,#0c2740 80%)"></div>
    <div class="project-label">PROJECT 6</div>
  </div>

  <a class="btn" style="left:506px;top:2448px;width:188px;height:43px;font-size:14px">VIEW ALL PROJECTS</a>
</section>

<section class="faq" role="img" aria-label="Photo of a happy family with arms outstretched in a sunlit meadow">
  <div class="faq-scene"></div>
  <div class="title-rule" style="left:552px;top:48px;width:100px"></div>
  <div class="dot-b" style="left:648px;top:43px"></div>
  <h2 class="section-title" style="left:500px;top:52px;width:200px;font-size:26px">FAQ</h2>
  <div class="title-rule under" style="left:548px;top:94px;width:104px"></div>
  <div class="dot-g" style="left:540px;top:90px"></div>

  <div class="faq-item" style="top:154px;width:329px">What makes this project unique?
    <span class="faq-toggle"><svg width="10" height="6" viewBox="0 0 10 6"><path d="M1 1 l4 4 4 -4" fill="none" stroke="#2a2a2a" stroke-width="1.4"/></svg></span></div>
  <div class="faq-item" style="top:227px;width:614px">Does this project assume that the impact of religion is always positive?
    <span class="faq-toggle"><svg width="10" height="6" viewBox="0 0 10 6"><path d="M1 1 l4 4 4 -4" fill="none" stroke="#2a2a2a" stroke-width="1.4"/></svg></span></div>
  <div class="faq-item" style="top:287px;width:231px">How can I collaborate?
    <span class="faq-toggle"><svg width="10" height="6" viewBox="0 0 10 6"><path d="M1 1 l4 4 4 -4" fill="none" stroke="#2a2a2a" stroke-width="1.4"/></svg></span></div>
  <div class="faq-item" style="top:366px;width:380px">Will Harrowgate U faculty lead all projects?
    <span class="faq-toggle"><svg width="10" height="6" viewBox="0 0 10 6"><path d="M1 1 l4 4 4 -4" fill="none" stroke="#2a2a2a" stroke-width="1.4"/></svg></span></div>
</section>

<footer class="site-footer">
  <div class="footer-brand">
    <div class="footer-brand-dot"></div>
    <div class="footer-brand-name">Wellness, Meaning, and the Inner Journey</div>
  </div>

  <div class="footer-heading" style="left:430px;top:48px">MENU</div>
  <ul class="footer-menu">
    <li>HOME</li><li>PEOPLE</li><li>PROJECTS</li><li>FAQS</li><li>RESOURCES</li><li>CONTACT</li>
  </ul>

  <div class="footer-heading" style="left:655px;top:48px">CONTACT US</div>
  <div class="contact-icon" style="left:652px;top:82px">
    <svg width="16" height="16" viewBox="0 0 24 24"><path d="M6.6 10.8a15 15 0 0 0 6.6 6.6l2.2-2.2a1 1 0 0 1 1-.25 11.4 11.4 0 0 0 3.6.57 1 1 0 0 1 1 1V20a1 1 0 0 1-1 1A17 17 0 0 1 3 4a1 1 0 0 1 1-1h3.5a1 1 0 0 1 1 1c0 1.25.2 2.45.57 3.6a1 1 0 0 1-.25 1z" fill="#1c1c1c"/></svg>
  </div>
  <div class="contact-text" style="left:704px;top:82px">Call Us<br>0400 555 018</div>
  <div class="contact-icon" style="left:861px;top:82px">
    <svg width="16" height="14" viewBox="0 0 24 20"><rect x="1" y="2" width="22" height="16" rx="2" fill="#1c1c1c"/><path d="M2 4 l10 7 10 -7" fill="none" stroke="#fff" stroke-width="1.8"/></svg>
  </div>
  <div class="contact-text" style="left:912px;top:82px">E mail Us<br>hello@innerjourney-study.org</div>

  <div class="footer-heading" style="left:655px;top:172px">FOLLOW US</div>
  <div class="social" style="left:746px;top:164px;background:#3a5cbf" aria-label="Social profile"></div>
  <div class="social" style="left:783px;top:164px;background:#1f9ad6" aria-label="Social profile"></div>
  <div class="social" style="left:820px;top:164px;background:#2f3e9e" aria-label="Social profile"></div>

  <div class="footer-rule"></div>
  <div class="copyright">Copyright © 2021 All Rights Reserved</div>
</footer>

</body>
</html>
```